Business Card for Field Lotus-Eco Friendly Organic Clothing Brand

We are looking for an amazing business card for our eco friendly, organic clothing brand. We are thinking maybe a business card with a peel off sticker on the back, since our hanging clothing tag is a peel off sticker on the back. I will attach our hang tag so we can make sure we stay in line with our design. I've also attached a bag we are doing because I do like the scattered emblem look as well.

```html
<!DOCTYPE html>
<html lang="en">
<head>
<meta charset="utf-8">
<title>Field Lotus – Business Card</title>
<link rel="stylesheet" href="https://fonts.googleapis.com/css2?family=Open+Sans:wght@400;600;700&display=swap">
<style>
  :root {
    --page: #e9e7e2;
    --card-dark: #232f1a;
    --card-light: #ffffff;
    --gold: #e6b820;
    --gold-deep: #b8891a;
    --olive: #6d7a3a;
    --ink-light: #f1ecd9;
    --tag-fill: #1f2a17;
  }
  * { margin: 0; padding: 0; box-sizing: border-box; }
  html, body { width: 1200px; height: 900px; overflow: hidden; }
  body {
    position: relative;
    background: var(--page);
    font-family: "Open Sans", Arial, sans-serif;
  }

  .card { position: absolute; width: 555px; height: 342px; }

  /* Front */
  .card-front { left: 240px; top: 62px; background: var(--card-dark); color: var(--ink-light); }
  .emblem-area {
    position: absolute; left: 42px; top: 56px;
    width: 210px; height: 210px; border-radius: 50%;
    background: radial-gradient(circle at 45% 40%, var(--gold) 0%, var(--olive) 70%, var(--gold-deep) 100%);
    opacity: .9;
  }
  .brand-name {
    position: absolute; right: 40px; top: 52px;
    font-weight: 700; font-size: 40px; line-height: 1; letter-spacing: 1px;
    color: var(--gold); text-align: right;
  }
  .person { position: absolute; right: 40px; top: 156px; text-align: right; }
  .person-name { font-weight: 600; font-size: 18px; color: var(--gold); line-height: 24px; }
  .person-role { font-size: 15px; line-height: 20px; }
  .contacts { position: absolute; right: 40px; top: 214px; list-style: none; }
  .contacts li {
    display: flex; justify-content: flex-end; align-items: center;
    font-size: 14.5px; line-height: 20px; gap: 9px;
  }
  .contacts svg { width: 11px; height: 11px; fill: var(--gold); }
  .address {
    position: absolute; left: 102px; top: 297px;
    font-size: 15px; color: var(--ink-light);
  }

  /* Back */
  .card-back { left: 458px; top: 518px; background: var(--card-light); }
  .hang-tag { position: absolute; left: 100px; top: 82px; }
  .tag-brand {
    position: absolute; left: 272px; top: 146px;
    font-weight: 700; font-size: 20px; line-height: 26px; letter-spacing: .5px;
    color: var(--gold); white-space: nowrap;
  }
  .tag-url {
    position: absolute; left: 272px; top: 207px;
    font-size: 11px; line-height: 14px; color: var(--ink-light);
  }
</style>
</head>
<body>

<section class="card card-front">
  <div class="emblem-area" role="img" aria-label="Brand emblem area in gold and olive camouflage tones"></div>
  <div class="brand-name">FIELD<br>LOTUS</div>
  <div class="person">
    <p class="person-name">Daniel Brooks</p>
    <p class="person-role">Managing Director</p>
  </div>
  <ul class="contacts">
    <li>044-987 654 321
      <svg viewBox="0 0 24 24"><path d="M6.6 10.8a15.2 15.2 0 0 0 6.6 6.6l2.2-2.2c.3-.3.7-.4 1-.2 1.1.4 2.3.6 3.6.6.6 0 1 .4 1 1V20c0 .6-.4 1-1 1A17 17 0 0 1 3 4c0-.6.4-1 1-1h3.5c.6 0 1 .4 1 1 0 1.3.2 2.5.6 3.6.1.3 0 .7-.2 1z"/></svg>
    </li>
    <li>hello@fieldlotus.com
      <svg viewBox="0 0 24 24"><path d="M2 5h20v14H2z" fill="var(--gold)"/><path d="M2 5l10 8 10-8" fill="none" stroke="var(--card-dark)" stroke-width="2"/></svg>
    </li>
    <li>www.fieldlotus.com
      <svg viewBox="0 0 24 24"><circle cx="12" cy="12" r="11"/><path d="M1 12h22M12 1c4 4 4 18 0 22M12 1c-4 4-4 18 0 22" fill="none" stroke="var(--card-dark)" stroke-width="1.6"/></svg>
    </li>
  </ul>
  <p class="address">12345, Address Goes Here Country Name, 123456.</p>
</section>

<section class="card card-back">
  <svg class="hang-tag" width="360" height="180" viewBox="0 0 360 180">
    <rect x="35" y="20" width="317" height="140" rx="12" fill="var(--tag-fill)" role="img" aria-label="Dark camouflage tag background"/>
    <rect x="43" y="28" width="301" height="124" rx="6" fill="none" stroke="var(--gold)" stroke-width="2"/>
    <circle cx="330" cy="90" r="4" fill="#ffffff"/>
    <polygon points="84,12 162,90 84,168 6,90" fill="var(--tag-fill)" stroke="var(--tag-fill)" stroke-width="6"/>
    <polygon points="84,27 147,90 84,153 21,90" fill="none" stroke="var(--gold)" stroke-width="2"/>
    <circle cx="84" cy="90" r="26" fill="var(--olive)" role="img" aria-label="Small brand emblem area"/>
  </svg>
  <div class="tag-brand">FIELD LOTUS</div>
  <div class="tag-url">www.fieldlotus.com</div>
</section>

</body>
</html>
```